Business Card Design

We need a business card designed for our new company. Prefer a black card with white logo & writing.

Contact Information for Business Card

Ted Galloway, address: 7-4812 Fernhollow Road, Abbotsford, BC, V3K 8R2, Office Phone: 604-712-3390, Cell: 604-947-2164, Email: ted@resinworkshub.ca

Colors

Designer to choose only greyscale colors for use in the design.

```html
<!DOCTYPE html>
<html lang="en">
<head>
<meta charset="utf-8">
<title>Resinworks Hub – Business Card</title>
<link rel="stylesheet" href="https://fonts.googleapis.com/css2?family=Montserrat:wght@400;600;700&display=swap">
<style>
  :root {
    --backdrop: #2b2b2b;
    --card: #141414;
    --ink: #ffffff;
    --ink-soft: #e6e6e6;
    --front-mark: #3a3a3a;
    --band: #ffffff;
    --band-text: #555555;
  }
  * { margin: 0; padding: 0; box-sizing: border-box; }
  html, body { width: 1200px; height: 1059px; overflow: hidden; }
  body {
    background: var(--backdrop);
    font-family: "Montserrat", sans-serif;
    position: relative;
  }
  .card {
    position: absolute;
    background: var(--card);
    border-radius: 20px;
    overflow: hidden;
  }
  .card-front { left: 256px; top: 89px; width: 688px; height: 390px; }
  .card-back { left: 252px; top: 546px; width: 696px; height: 394px; }

  .brand-name {
    position: absolute;
    left: 0; right: 0;
    text-align: center;
    font-weight: 700;
    letter-spacing: 1px;
    white-space: nowrap;
  }
  .card-front .brand-name { top: 168px; font-size: 44px; color: var(--front-mark); }
  .card-back .brand-name { top: 98px; font-size: 32px; color: var(--ink); }

  .person {
    position: absolute;
    right: 369px;
    top: 241px;
    text-align: right;
    color: var(--ink);
  }
  .person-name { font-size: 30px; font-weight: 600; line-height: 36px; }
  .person-title { font-size: 18px; font-weight: 400; color: var(--ink-soft); margin-top: 4px; }

  .divider {
    position: absolute;
    left: 353px; top: 245px;
    width: 2px; height: 72px;
    background: var(--ink);
  }

  .contacts {
    position: absolute;
    left: 376px; top: 238px;
    list-style: none;
    color: var(--ink);
    font-size: 18.5px;
    font-weight: 400;
  }
  .contacts li { display: flex; align-items: center; height: 27px; }
  .contacts svg { width: 16px; height: 16px; margin-right: 10px; fill: var(--ink); flex: none; }

  .address-band {
    position: absolute;
    left: 0; right: 0; top: 346px;
    height: 24px;
    background: var(--band);
  }
  .address {
    position: absolute;
    left: 0; right: 52px;
    top: 0; line-height: 24px;
    text-align: center;
    font-size: 18px;
    color: var(--band-text);
  }
  .band-dot {
    position: absolute;
    left: 622px; top: -3px;
    width: 30px; height: 30px;
    border-radius: 50%;
    background: #333333;
    border: 2px solid var(--band);
  }
</style>
</head>
<body>
  <section class="card card-front" aria-label="Card front">
    <div class="brand-name">RESINWORKS HUB</div>
  </section>

  <section class="card card-back" aria-label="Card back">
    <div class="brand-name">RESINWORKS HUB</div>

    <div class="person">
      <div class="person-name">Ted Galloway</div>
      <div class="person-title">Owner/CEO</div>
    </div>

    <div class="divider"></div>

    <ul class="contacts">
      <li>
        <svg viewBox="0 0 16 16" aria-hidden="true"><path d="M2 6c0-2 2-3 6-3s6 1 6 3v1h-3V5.5H5V7H2zM4 8h8l2 5H2z"/></svg>
        604-712-3390
      </li>
      <li>
        <svg viewBox="0 0 16 16" aria-hidden="true"><path d="M4 1h8v14H4zM5.5 2.5v9.5h5V2.5zM7 13h2v1H7z" fill-rule="evenodd"/></svg>
        604-947-2164
      </li>
      <li>
        <svg viewBox="0 0 16 16" aria-hidden="true"><path d="M1 5l7 5 7-5v9H1zM1 4h14L8 9z"/></svg>
        ted@resinworkshub.ca
      </li>
    </ul>

    <div class="address-band">
      <div class="address">7-4812 Fernhollow Road, Abbotsford, BC, V3K 8R2</div>
      <div class="band-dot"></div>
    </div>
  </section>
</body>
</html>
```